High Tech Real Estate Startup needs a business card

We are developing an innovative real estate marketing product based around advanced search and virtual reality.

We talk to people, we need business cards.

Target Market(s)

The target market is technology professionals and realtors.

Contact Information for Business Card

The information to be included will include

Name
Title
Phone Number
E-mail Address
www.zelquin.com

It should use simple iconography for each one of those fields.

Font styles to use
Other font styles liked:
• Co, Jubilat, Avenir

Colors

Designer to choose colors to be used in the design.

Requirements
Must have
• Clean aesthetic,
• Good use of negative space.
• It should use our company logo, shown in the attached file. It is able to use the negative of that logo (coloured font and white background) and I have attached other acceptable accent colours in a swatch file.
Should not have
• Should not be too busy
• No extraneous text (slogans, tag lines etc)

```html
<!DOCTYPE html>
<html lang="en">
<head>
<meta charset="utf-8">
<title>Zelquin Business Card</title>
<link rel="stylesheet" href="https://fonts.googleapis.com/css2?family=Montserrat:wght@500&family=Open+Sans:wght@400;600&display=swap">
<style>
  :root {
    --backdrop: #2b2b2d;
    --teal: #3fb7b3;
    --teal-deep: #2e9e9a;
    --paper: #f4f4f2;
    --ink: #555a5c;
    --ink-soft: #7b8082;
    --icon: #9aa0a2;
  }
  * { margin: 0; padding: 0; box-sizing: border-box; }
  html, body { width: 800px; height: 1200px; overflow: hidden; }
  body {
    background: var(--backdrop);
    display: flex;
    flex-direction: column;
    align-items: center;
    justify-content: space-around;
    font-family: "Open Sans", sans-serif;
  }
  .card {
    width: 640px;
    height: 366px;
    border-radius: 18px;
    position: relative;
    overflow: hidden;
    box-shadow: 0 14px 30px rgba(0,0,0,.45);
  }
  .card-front {
    background: var(--teal);
    display: flex;
    align-items: center;
    justify-content: center;
  }
  .wordmark {
    font-family: "Montserrat", sans-serif;
    font-weight: 500;
    letter-spacing: 4px;
    white-space: nowrap;
  }
  .card-front .wordmark {
    font-size: 72px;
    color: var(--teal-deep);
  }
  .card-back { background: var(--paper); }
  .side-band {
    position: absolute;
    left: 0; top: 0; bottom: 0;
    width: 40px;
    background: var(--teal);
  }
  .card-back .wordmark {
    position: absolute;
    left: 90px; top: 84px;
    font-size: 64px;
    color: var(--teal);
  }
  .identity {
    position: absolute;
    left: 90px; top: 200px;
  }
  .person-name {
    font-size: 24px;
    font-weight: 600;
    color: var(--teal);
  }
  .person-title {
    font-size: 13px;
    color: var(--ink);
    margin-top: 2px;
  }
  .contact-list {
    list-style: none;
    margin-top: 14px;
  }
  .contact-list li {
    display: flex;
    align-items: center;
    gap: 8px;
    font-size: 12px;
    color: var(--ink-soft);
    line-height: 20px;
  }
  .contact-icon { width: 14px; height: 14px; flex: none; }
</style>
</head>
<body>
  <section class="card card-front">
    <span class="wordmark">ZELQUIN</span>
  </section>

  <section class="card card-back">
    <div class="side-band"></div>
    <span class="wordmark">ZELQUIN</span>
    <div class="identity">
      <p class="person-name">Jane Rowe Carter</p>
      <p class="person-title">Managing Director</p>
      <ul class="contact-list">
        <li>
          <svg class="contact-icon" viewBox="0 0 14 14"><circle cx="7" cy="7" r="7" fill="#9aa0a2"/><rect x="5" y="3" width="4" height="8" rx="1" fill="#fff"/></svg>
          312.480.9167
        </li>
        <li>
          <svg class="contact-icon" viewBox="0 0 14 14"><circle cx="7" cy="7" r="7" fill="#9aa0a2"/><rect x="3.5" y="4.5" width="7" height="5" fill="#fff"/><path d="M3.5 4.5 L7 7.5 L10.5 4.5" stroke="#9aa0a2" stroke-width=".8" fill="none"/></svg>
          jane@zelquin.com
        </li>
        <li>
          <svg class="contact-icon" viewBox="0 0 14 14"><circle cx="7" cy="7" r="7" fill="#9aa0a2"/><circle cx="7" cy="7" r="3.5" stroke="#fff" stroke-width=".9" fill="none"/><path d="M3.5 7 H10.5 M7 3.5 V10.5" stroke="#fff" stroke-width=".8"/></svg>
          www.zelquin.com
        </li>
      </ul>
    </div>
  </section>
</body>
</html>
```